Business Card and Letterhead for Pimlu - modern real estate business

I need a double sided business card design for Pimlu. Please see business card brief here https://files.trelvonadocs.com/sheet/r/7QzTmWbaXLJnoPEd-kRyUgFhHsstbvCe2qfoMxDa_pz/view?mode=shared

Please feel free to design the business cards however you feel best. I am happy to give some creative freedoms and then provide feedback from there.

Please then also create a letterhead to match the business card design

Colors

Designer to choose colors to be used in the design.

Requirements
Must have
• Must be a modern, elegant business card which looks very professional

```html
<!DOCTYPE html>
<html lang="en">
<head>
<meta charset="utf-8">
<title>Pimlu – Business Card</title>
<link rel="stylesheet" href="https://fonts.googleapis.com/css2?family=Roboto:wght@400;500;700&display=swap">
<style>
  :root {
    --stage: #2b2b2b;
    --brand-red: #e31e26;
    --brand-red-light: #ef5a60;
    --brand-red-dark: #b5151c;
    --ink: #141414;
    --card-white: #f7f7f7;
    --card-black: #000000;
    --photo-light: #e9e6e4;
    --photo-dark: #2e2f33;
  }
  html, body {
    margin: 0;
    width: 1200px;
    height: 865px;
    overflow: hidden;
    background: var(--stage);
    font-family: "Roboto", Arial, sans-serif;
  }
  .sheet {
    width: 1200px;
    height: 865px;
    display: flex;
    flex-direction: column;
    align-items: center;
    justify-content: center;
    gap: 40px;
  }
  .card {
    display: block;
    width: 640px;
    height: 366px;
    filter: drop-shadow(0 10px 18px rgba(0,0,0,0.45));
  }
  .wordmark { font-family: "Roboto", Arial, sans-serif; font-weight: 700; fill: var(--brand-red); letter-spacing: 6px; }
  .agent-name { font-weight: 700; fill: var(--brand-red); font-size: 27px; letter-spacing: 2px; }
  .agent-title { font-weight: 500; fill: var(--ink); font-size: 17px; }
  .detail { font-weight: 500; fill: var(--ink); font-size: 16px; }
  .detail-accent { fill: var(--brand-red); }
  .licence { font-weight: 500; fill: #ffffff; font-size: 15px; }
  .icon-badge { fill: var(--ink); }
  .icon-line { fill: none; stroke: #ffffff; stroke-width: 1.4; stroke-linecap: round; stroke-linejoin: round; }
</style>
</head>
<body>
<main class="sheet">

  <!-- Card back -->
  <svg class="card card-back" viewBox="0 0 640 366" aria-label="Business card back">
    <rect width="640" height="366" rx="22" fill="var(--card-black)"/>
    <text class="wordmark" x="320" y="228" text-anchor="middle" font-size="130">PIMLU</text>
  </svg>

  <!-- Card front -->
  <svg class="card card-front" viewBox="0 0 640 366" aria-label="Business card front">
    <defs>
      <clipPath id="card-shape"><rect width="640" height="366" rx="22"/></clipPath>
      <linearGradient id="photo-tone" x1="0" y1="0" x2="0" y2="1">
        <stop offset="0" stop-color="var(--photo-light)"/>
        <stop offset="0.35" stop-color="#b9a396"/>
        <stop offset="0.5" stop-color="var(--photo-dark)"/>
        <stop offset="1" stop-color="#1d1e21"/>
      </linearGradient>
      <linearGradient id="wave-tone" x1="0" y1="0" x2="0" y2="1">
        <stop offset="0" stop-color="var(--brand-red)"/>
        <stop offset="1" stop-color="var(--brand-red-dark)"/>
      </linearGradient>
    </defs>
    <g clip-path="url(#card-shape)">
      <rect width="640" height="366" fill="var(--card-white)"/>

      <rect class="agent-photo" x="400" y="36" width="230" height="250" rx="4"
            fill="url(#photo-tone)" role="img"
            aria-label="Portrait photo of the agent in a dark blazer"/>

      <path class="wave-highlight" d="M0,342 C220,356 330,330 430,258 C510,200 570,168 640,156 L640,366 L0,366 Z" fill="var(--brand-red-light)"/>
      <path class="wave-band" d="M0,350 C220,364 336,340 436,270 C514,214 572,184 640,172 L640,366 L0,366 Z" fill="url(#wave-tone)"/>

      <text class="licence" x="500" y="318" transform="rotate(-22 500 318)">Lic No. 30418826</text>
    </g>

    <text class="wordmark" x="42" y="86" font-size="60">PIMLU</text>

    <rect class="name-bar" x="42" y="118" width="7" height="50" fill="var(--brand-red)"/>
    <text class="agent-name" x="60" y="141">DANE CARROW</text>
    <text class="agent-title" x="60" y="164">Licenced Real Estate Agent</text>

    <text class="detail" x="72" y="198">PO Box 5190</text>
    <text class="detail" x="72" y="218">Kelsbrook NSW 2841</text>

    <!-- mobile -->
    <circle class="icon-badge" cx="92" cy="244" r="10"/>
    <rect class="icon-line" x="88.5" y="238" width="7" height="12" rx="1.2"/>
    <text class="detail" x="110" y="250">0412 608 391</text>

    <!-- landline -->
    <circle class="icon-badge" cx="92" cy="270" r="10"/>
    <path class="icon-line" d="M87,266 q0,-2 2,-2 l1.5,2.5 -1.5,1.5 q1.5,3 4.5,4.5 l1.5,-1.5 2.5,1.5 q0,2 -2,2 q-8,-1 -8.5,-8.5z"/>
    <text class="detail" x="110" y="276">1300 555 018</text>

    <!-- email -->
    <circle class="icon-badge" cx="92" cy="296" r="10"/>
    <rect class="icon-line" x="86" y="291.5" width="12" height="9" rx="1"/>
    <path class="icon-line" d="M86,292 l6,5 6,-5"/>
    <text class="detail" x="110" y="302">dane@pimlu.com</text>

    <!-- web -->
    <circle class="icon-badge" cx="92" cy="322" r="10"/>
    <circle class="icon-line" cx="92" cy="322" r="5.5"/>
    <path class="icon-line" d="M86.5,322 h11 M92,316.5 q-3,5.5 0,11 M92,316.5 q3,5.5 0,11"/>
    <text class="detail" x="110" y="328">www.<tspan class="detail-accent">pimlu</tspan>.com</text>
  </svg>

</main>
</body>
</html>
```